Rock Bag Packaging Design

Hey Guys! Hope All is well. I need a designer to make artwork for a cubic foot poly bag. I will packaging rocks into 1 cubic foot bags that measure 18" x 29". The rocks are to be used for drainage, aquaponics, hydroponics, and even decorative ground cover. The rock is very comparable to Brimfield Pebbles and I will be competing against them and other companies like Tarnlites, Vexo!k, AquaBrell, Pelvarin, Fennick Grove Clay Pellets, Moss Vane, just to name a few.
The bags will be clear and color will be printed over it. Need 25%-50% of the bag to be clear to show the rocks. The design can be made to show the rocks in a cool way.
I'm looking for the design to be simple and professional with a earth friendly, green thumb feel.
Information to include on bag...
The product is called 'Tumble Pipz'. This name needs a cool logo.
Reasons to Buy:
-pH Neutral
-Chemically Inert
-Excellent Air to Water Ratio
-Reusable
Uses:
-Decoration
-Drainage
-Hydroponics
-Aquaponics
1 Cu. Ft. (47 LBS)
MADE IN U.S.A.
Updates
Hey All,
Target Market(s)
Hobby/Professional Gardeners
Industry/Entity Type
Product
Requirements
Must have
- Earth Friendly Feel
Feeling that this stuff can grow huge healthy fruits/flowers /root systems

```html
<!DOCTYPE html>
<html lang="en">
<head>
<meta charset="UTF-8">
<title>Tumble Pipz – 1 Cu. Ft. Bag Artwork</title>
<link href="https://fonts.googleapis.com/css2?family=Dosis:wght@600;700;800&display=swap" rel="stylesheet">
<style>
  :root {
    --leaf-light: #86c043;
    --leaf-dark: #00733a;
    --leaf-mid: #1f8a3e;
    --bag-clear: #ffffff;
    --frame-line: #d6d6d6;
    --ink-white: #ffffff;
  }
  * { margin: 0; padding: 0; box-sizing: border-box; }
  html, body {
    width: 777px; height: 1200px; overflow: hidden;
    background: #ffffff;
  }
  .bag {
    position: relative;
    width: 777px; height: 1200px;
    font-family: "Dosis", sans-serif;
  }
  .bag-panel {
    position: absolute;
    left: 42px; top: 42px; width: 688px; height: 1110px;
    background: var(--bag-clear);
    border: 1px solid var(--frame-line);
    overflow: hidden;
  }
  .print-zone {
    position: absolute; left: 0; top: 0; width: 100%; height: 820px;
    background: var(--leaf-light);
  }
  .brand-name {
    position: absolute; left: 0; top: 86px; width: 100%;
    text-align: center;
    font-weight: 800; font-size: 80px; line-height: 1;
    letter-spacing: 1px;
    color: var(--leaf-dark);
  }
  .feature-list {
    position: absolute; list-style: none;
    font-weight: 700; font-size: 30px; line-height: 1;
    color: var(--leaf-dark);
  }
  .feature-list li {
    position: absolute; left: 0; white-space: nowrap;
    padding-left: 38px;
  }
  .feature-list li::before {
    content: ""; position: absolute; left: 0; top: 2px;
    width: 26px; height: 26px; border-radius: 50%;
    background: var(--ink-white);
  }
  .feature-list .two-line { line-height: 0.88; }
  .benefits { left: 98px; top: 204px; }
  .uses { left: 398px; top: 204px; }
  .plant-scene {
    position: absolute; left: 0; top: 420px; width: 688px; height: 420px;
  }
  .volume-tag {
    position: absolute; left: 198px; top: 900px; width: 292px; height: 51px;
    border-radius: 12px; background: var(--leaf-light);
    color: var(--leaf-dark);
    font-weight: 800; font-size: 29px;
    display: flex; align-items: center; justify-content: center;
  }
  .origin {
    position: absolute; left: 0; top: 972px; width: 100%;
    text-align: center;
    font-weight: 600; font-size: 31px;
    color: var(--leaf-light);
  }
</style>
</head>
<body>
<main class="bag">
  <section class="bag-panel">
    <div class="print-zone"></div>

    <h1 class="brand-name">TUMBLE PIPZ</h1>

    <ul class="feature-list benefits">
      <li style="top:0">pH Neutral</li>
      <li style="top:48px">Chemically Inert</li>
      <li style="top:96px" class="two-line">Excellent Air<br>to Water Ratio</li>
      <li style="top:171px">Reusable</li>
    </ul>

    <ul class="feature-list uses">
      <li style="top:0">Decoration</li>
      <li style="top:48px">Drainage</li>
      <li style="top:96px">Hydroponics</li>
      <li style="top:153px">Aquaponics</li>
    </ul>

    <svg class="plant-scene" viewBox="0 0 688 420" role="img" aria-label="Silhouettes of tropical plants and grass growing over a ridge of rocks">
      <defs>
        <linearGradient id="foliage" x1="0" y1="0" x2="0" y2="1">
          <stop offset="0" stop-color="#1f8a3e"/>
          <stop offset="1" stop-color="#00733a"/>
        </linearGradient>
      </defs>
      <path d="M0 80 L688 60 L688 400 L610 330 L520 300 L420 310 L300 290 L180 300 L110 320 L60 340 L0 330 Z" fill="url(#foliage)"/>
    </svg>

    <div class="volume-tag">1 Cu. Ft. (47 LBS)</div>
    <p class="origin">MADE IN U.S.A.</p>
  </section>
</main>
</body>
</html>
```